BOLD & MINIMALIST DESIGN NEEDED

We want a very bold but minimalistic business card design that is impactful and utilizes both sides of the business card. Our current logo is included for your use.

We want bold fonts and good use of negative space. We don't want the logo to overpower the design.

Target Market(s)

Professionals who are building new commercial buildings.

Industry/Entity Type

Construction

Contact Information for Business Card

Name, Title, email, office phone, cell phone, website

Font styles to use
Serif
Sans Serif

Requirements
Must have
• Bold design!

```html
<!DOCTYPE html>
<html lang="en">
<head>
<meta charset="utf-8">
<title>Ridgeform Business Card</title>
<link rel="stylesheet" href="https://fonts.googleapis.com/css2?family=Poppins:wght@400;600;800&display=swap">
<style>
  :root {
    --backdrop: #5e4631;
    --brand-green: #86c449;
    --brand-green-light: #a0d160;
    --accent-green: #7cc142;
    --ink: #111111;
    --paper: #ffffff;
  }
  html, body {
    margin: 0;
    padding: 0;
    width: 1189px;
    height: 1200px;
    overflow: hidden;
    background: var(--backdrop);
    font-family: "Poppins", sans-serif;
  }
  .canvas {
    position: relative;
    width: 1189px;
    height: 1200px;
  }
  .card {
    position: absolute;
    left: 169px;
    width: 851px;
    height: 485px;
    border-radius: 37px;
    box-shadow: 0 8px 22px rgba(0, 0, 0, 0.45);
    overflow: hidden;
  }
  .card-front {
    top: 112px;
    background: radial-gradient(ellipse at 50% 45%, var(--brand-green-light) 0%, var(--brand-green) 75%);
    display: flex;
    align-items: center;
    justify-content: center;
  }
  .card-back {
    top: 640px;
    background: var(--paper);
  }
  .brand-name {
    margin: 0;
    font-weight: 800;
    color: var(--ink);
    letter-spacing: 1px;
    line-height: 1;
  }
  .card-front .brand-name {
    font-size: 60px;
  }
  .card-back .brand-name {
    position: absolute;
    left: 0;
    width: 440px;
    top: 272px;
    text-align: center;
    font-size: 46px;
  }
  .contact-block {
    position: absolute;
    left: 436px;
    top: 137px;
    color: var(--ink);
  }
  .person {
    border-left: 3px solid var(--accent-green);
    padding-left: 22px;
    height: 46px;
  }
  .person-name {
    margin: 0;
    font-weight: 600;
    font-size: 29px;
    line-height: 30px;
    margin-top: -4px;
  }
  .person-title {
    margin: 0;
    font-size: 19px;
    line-height: 22px;
    color: var(--accent-green);
  }
  .address {
    margin: 47px 0 0 0;
    font-size: 20px;
    line-height: 25px;
  }
  .contact-list {
    list-style: none;
    margin: 10px 0 0 0;
    padding: 0;
    font-size: 21px;
    line-height: 28px;
  }
  .contact-list li {
    display: flex;
    align-items: center;
  }
  .contact-icon {
    width: 16px;
    height: 16px;
    margin-right: 16px;
    flex: none;
  }
</style>
</head>
<body>
<main class="canvas">
  <section class="card card-front">
    <h1 class="brand-name">RIDGEFORM</h1>
  </section>

  <section class="card card-back">
    <h2 class="brand-name">RIDGEFORM</h2>

    <div class="contact-block">
      <div class="person">
        <p class="person-name">DANIEL REYES</p>
        <p class="person-title">Craftsman</p>
      </div>
      <p class="address">PO BOX 418 Kerr Lane<br>7th Avenue Brunswick</p>
      <ul class="contact-list">
        <li>
          <svg class="contact-icon" viewBox="0 0 16 16" aria-hidden="true">
            <path d="M4 1.5 L6.2 4.8 L4.9 6.3 C5.7 8.3 7.4 10.3 9.4 11.3 L10.9 9.9 L14 12.2 L12.4 14.5 C7.5 14.2 2.2 8.6 1.8 3.4 Z" fill="var(--accent-green)"/>
          </svg>
          (555) 204-3187
        </li>
        <li>
          <svg class="contact-icon" viewBox="0 0 16 16" aria-hidden="true">
            <rect x="1" y="3" width="14" height="10" fill="var(--accent-green)"/>
            <path d="M1 3 L8 9 L15 3 M1 13 L6 8 M15 13 L10 8" stroke="#ffffff" stroke-width="1.2" fill="none"/>
          </svg>
          info@ridgeform.com.au
        </li>
      </ul>
    </div>
  </section>
</main>
</body>
</html>
```